Thornvale Group needs a business card design

We need a new business card design using the logo recently selected in a logo competition on Pixel Bazaar. Our business is a consultancy specializing in aviation and energy and the winning business card design will promote an image of precision and professionalism with creativity.

Please use the logo with the name on the front of the card and use a complementary font. Make the back white with either the light grey or dark grey logo.

Target Market(s)

Senior finance and legal leaders at aviation and energy companies

Industry/Entity Type

Management Consulting

Contact Information for Business Card

Peter Castrell
President
Thornvale Group

www.thornvalegroup.example

(555) 204-6391
pc@thornvalegroup.example

Requirements
Must have
• Professional font that goes well with the logo font

```html
<!DOCTYPE html>
<html lang="en">
<head>
<meta charset="utf-8">
<title>Thornvale Group — Business Card</title>
<link rel="stylesheet" href="https://fonts.googleapis.com/css2?family=Open+Sans:wght@400;700&display=swap">
<style>
  :root {
    --page-bg: #e6e7eb;
    --front-top: #a3a7ac;
    --front-bottom: #4c5055;
    --lavender: #d3d6e8;
    --lavender-deep: #b9bdd6;
    --brand-blue: #1f5a8a;
    --navy: #1d3c63;
    --white: #ffffff;
    --back-top: #f1f2f8;
    --back-bottom: #b6bad4;
  }
  * { margin: 0; padding: 0; box-sizing: border-box; }
  html, body {
    width: 1200px; height: 913px; overflow: hidden;
    background: var(--page-bg);
    font-family: "Open Sans", Arial, sans-serif;
  }
  .canvas { position: relative; width: 1200px; height: 913px; }
  .card {
    position: absolute; width: 520px; height: 297px;
    border-radius: 16px; overflow: hidden;
    box-shadow: 0 10px 24px rgba(0,0,0,.22);
  }
  .card-front { left: 50px; top: 190px; }
  .card-back {
    left: 630px; top: 430px;
    background: linear-gradient(170deg, var(--back-top) 0%, var(--back-bottom) 100%);
  }
  .card-art { position: absolute; inset: 0; }
  .brand-name {
    position: absolute; color: var(--brand-blue);
    font-weight: 400; letter-spacing: 1px; white-space: nowrap;
  }
  .card-front .brand-name { left: 34px; top: 100px; font-size: 24px; }
  .card-back .brand-name {
    left: 0; right: 0; top: 124px; text-align: center; font-size: 36px;
  }
  .person { position: absolute; right: 82px; top: 72px; text-align: right; }
  .person-name { color: var(--white); font-weight: 700; font-size: 22px; line-height: 1.1; }
  .person-title { color: var(--brand-blue); font-size: 12px; margin-top: 2px; }
  .contact {
    position: absolute; left: 200px; top: 218px;
    list-style: none; color: var(--navy); font-size: 13px; line-height: 19px;
  }
</style>
</head>
<body>
<main class="canvas">
  <section class="card card-front" aria-label="Card front">
    <svg class="card-art" viewBox="0 0 520 297" aria-hidden="true">
      <defs>
        <linearGradient id="frontGrey" x1="0" y1="0" x2="0" y2="1">
          <stop offset="0" stop-color="var(--front-top)"/>
          <stop offset="1" stop-color="var(--front-bottom)"/>
        </linearGradient>
        <linearGradient id="bandLavender" x1="0" y1="0" x2="1" y2="1">
          <stop offset="0" stop-color="var(--lavender)"/>
          <stop offset="1" stop-color="var(--lavender-deep)"/>
        </linearGradient>
      </defs>
      <rect width="520" height="297" fill="url(#frontGrey)"/>
      <rect x="452" y="44" width="40" height="40" fill="#d9dbe6"/>
      <line x1="150" y1="150" x2="440" y2="120" stroke="var(--brand-blue)" stroke-width="1"/>
      <polygon class="contact-band" points="0,232 520,150 520,297 0,297" fill="url(#bandLavender)"/>
      <polygon class="icon-panel" points="0,222 185,297 0,297" fill="var(--brand-blue)"/>
      <g class="icon-stripes" fill="var(--white)">
        <rect x="62" y="250" width="96" height="9"/>
        <rect x="62" y="265" width="96" height="9"/>
        <rect x="62" y="280" width="96" height="9"/>
      </g>
      <g class="icons" fill="none" stroke="var(--navy)" stroke-width="1.2">
        <path d="M110 251.5 q0 6 6 6 l1.5 -1.5 -2 -2 -1 1 q-2 -1 -3 -3 l1 -1 -2 -2z"/>
        <rect x="108" y="266.5" width="9" height="6"/>
        <path d="M108 266.5 l4.5 3.5 4.5 -3.5"/>
        <circle cx="112.5" cy="284.5" r="3.6"/>
        <line x1="108.9" y1="284.5" x2="116.1" y2="284.5"/>
      </g>
    </svg>
    <p class="brand-name">Thornvale Group</p>
    <div class="person">
      <p class="person-name">Peter Castrell</p>
      <p class="person-title">President</p>
    </div>
    <ul class="contact">
      <li>(555) 204-6391</li>
      <li>pc@thornvalegroup.example</li>
      <li>www.thornvalegroup.example</li>
    </ul>
  </section>

  <section class="card card-back" aria-label="Card back">
    <p class="brand-name">Thornvale Group</p>
  </section>
</main>
</body>
</html>
```